Business cards and stationary design

We just completed the design of our new logo and we need to print new business cards and letterhead for our nonprofit. We are looking for a fresh new design that shows off our new logo. On letterhead, we must have a column on the right or left to include our Board of Directors (up to 45 names) (see attachment)

Industry/Entity Type

Non-Profit

Contact Information for Business Card

Standard business card with name, title, Company name, mailing address phone numbers, email address and website. Tagline on back "Bringing the homeless home"

Font styles to use
Sans Serif

Requirements
Must have
• include pertinent information above
• new logo
• fonts compatible with logo
• should use logo colors only
Nice to have
• tag lines

```html
<!DOCTYPE html>
<html lang="en">
<head>
<meta charset="utf-8">
<title>Harbor Home Center – Business Card</title>
<link rel="stylesheet" href="https://fonts.googleapis.com/css2?family=Roboto:wght@400;500;700&family=Roboto+Condensed:wght@700&display=swap">
<style>
  :root {
    --backdrop: #2a2a2a;
    --brand-red: #d82027;
    --brand-teal: #0185a4;
    --paper: #f2f2f2;
    --ink: #4a4a4a;
    --white: #ffffff;
  }
  * { margin: 0; padding: 0; box-sizing: border-box; }
  html, body { width: 1200px; height: 960px; overflow: hidden; }
  body {
    background: var(--backdrop);
    font-family: "Roboto", Arial, sans-serif;
    position: relative;
  }
  .card {
    position: absolute;
    left: 320px;
    width: 600px;
    height: 342px;
    overflow: hidden;
  }
  /* Front */
  .card-front {
    top: 102px;
    background: var(--brand-red);
    color: var(--white);
  }
  .front-mark {
    position: absolute;
    left: 0; right: 0; top: 160px;
    display: flex;
    align-items: center;
    justify-content: center;
    gap: 14px;
  }
  .front-mark .dot {
    width: 22px; height: 22px;
    border-radius: 50%;
    background: var(--white);
  }
  .front-mark .org-name {
    font-size: 34px;
    font-weight: 500;
    letter-spacing: 3px;
    text-transform: uppercase;
  }
  .front-url {
    position: absolute;
    left: 0; right: 0; top: 297px;
    text-align: center;
    font-size: 14px;
    letter-spacing: 5px;
  }
  /* Back */
  .card-back { top: 493px; background: var(--paper); }
  .card-back .wave { position: absolute; inset: 0; }
  .person {
    position: absolute;
    right: 26px; top: 24px;
    text-align: right;
    color: var(--white);
  }
  .person-name {
    font-family: "Roboto Condensed", "Arial Narrow", sans-serif;
    font-size: 23px;
    font-weight: 700;
  }
  .person-title {
    font-size: 14px;
    font-weight: 500;
    margin-top: 3px;
  }
  .org-lockup {
    position: absolute;
    left: 34px; top: 192px;
    display: flex;
    align-items: center;
    gap: 10px;
    color: var(--brand-teal);
  }
  .org-lockup .dot {
    width: 14px; height: 14px;
    border-radius: 50%;
    background: var(--brand-teal);
  }
  .org-lockup .org-name {
    font-size: 20px;
    font-weight: 500;
    letter-spacing: 2.5px;
    text-transform: uppercase;
  }
  .contact-list {
    position: absolute;
    left: 32px; top: 266px;
    list-style: none;
    font-size: 14px;
    color: var(--ink);
    line-height: 19px;
  }
  .contact-list li { display: flex; align-items: center; gap: 8px; }
  .contact-list svg { width: 13px; height: 13px; fill: var(--brand-teal); }
  .address {
    position: absolute;
    right: 27px; top: 268px;
    text-align: right;
    font-size: 14px;
    color: var(--ink);
    line-height: 19px;
    font-style: normal;
  }
  .address .org-line { font-weight: 700; }
</style>
</head>
<body>

<section class="card card-front" aria-label="Business card front">
  <div class="front-mark">
    <span class="dot"></span>
    <span class="org-name">Harbor Home Center</span>
  </div>
  <p class="front-url">www.harborhome.org</p>
</section>

<section class="card card-back" aria-label="Business card back">
  <svg class="wave" viewBox="0 0 600 342" preserveAspectRatio="none" aria-hidden="true">
    <rect width="600" height="342" fill="var(--brand-teal)"/>
    <path d="M0,128 Q230,8 600,182 L600,342 L0,342 Z" fill="var(--brand-red)" stroke="var(--white)" stroke-width="2"/>
    <path d="M0,160 Q250,38 600,186 L600,342 L0,342 Z" fill="var(--paper)" stroke="var(--white)" stroke-width="1.5"/>
  </svg>

  <div class="person">
    <div class="person-name">DANIEL REYES</div>
    <div class="person-title">CEO/FOUNDER</div>
  </div>

  <div class="org-lockup">
    <span class="dot"></span>
    <span class="org-name">Harbor Home Center</span>
  </div>

  <ul class="contact-list">
    <li>
      <svg viewBox="0 0 24 24" aria-hidden="true"><path d="M6.6 10.8a15.1 15.1 0 0 0 6.6 6.6l2.2-2.2a1 1 0 0 1 1-.25 11.4 11.4 0 0 0 3.6.57 1 1 0 0 1 1 1V20a1 1 0 0 1-1 1A17 17 0 0 1 3 4a1 1 0 0 1 1-1h3.5a1 1 0 0 1 1 1c0 1.25.2 2.45.57 3.57a1 1 0 0 1-.25 1z"/></svg>
      555 014 2290
    </li>
    <li>
      <svg viewBox="0 0 24 24" aria-hidden="true"><path d="M2 5h20v14H2z M3.5 6.5 12 13l8.5-6.5" fill="var(--brand-teal)" stroke="var(--paper)" stroke-width="1.5"/></svg>
      daniel@harborhome.org
    </li>
    <li>
      <svg viewBox="0 0 24 24" aria-hidden="true"><circle cx="12" cy="12" r="10"/><path d="M2 12h20M12 2c3 3 3 17 0 20M12 2c-3 3-3 17 0 20" fill="none" stroke="var(--paper)" stroke-width="1.3"/></svg>
      www.harborhome.org
    </li>
  </ul>

  <address class="address">
    <div class="org-line">Harbor home center</div>
    <div>1240 Alder Street</div>
    <div>Fairbanks, Alaska 99701</div>
  </address>
</section>

</body>
</html>
```